Tablet App design for business management system

TaskOra is a business management system made especially for service based businesses (our subscribers). It enables systemising your service businesses. This can be used by diverse industries like automotive service, beauty (hair salons, nail spas), Spas, Chiropractor, acupuntcure, osteo, yoga studio, business coach, etc.

The UI of the app needs to be designed using flat and clean UI design trends that are currently prevailing for B2C apps. Even the sliding menu panel can be removed and alternative placement of this functionality can be suggested. The color palette used for the design should be limited (3-5 colours)

The Current UI screens are open to suggestions for change. For ease of management in minimum steps, consolidation of functionality on different screens can be suggested, accompanies by a rational reason with the objective of having a simple and straight forward user experience.

User should be able to move from one function to another (booking > view appointments > profile) in no more than 1 or max 2 gestures.

Target Market(s)

SME businesses that provide time based services

Industry/Entity Type

Business

Font styles to use
Sans Serif

Requirements
Must have
• The power point slides give a detailed account of the process flow and functionality that the app is to follow.
• Reference this slide to ensure that your final design must have all screens that are required to deliver the functionality.

```html
<!DOCTYPE html>
<html lang="en">
<head>
<meta charset="utf-8">
<title>TaskOra – Client Profile</title>
<link href="https://fonts.googleapis.com/css2?family=Roboto:wght@400;500&display=swap" rel="stylesheet">
<style>
  :root {
    --green: #5aaf80;
    --blue: #3f51b5;
    --cyan: #6fd6f2;
    --ink: #333b3a;
    --label: #6a7070;
    --icon: #7d8382;
    --field: rgba(255,255,255,0.42);
    --field-line: rgba(255,255,255,0.7);
    --tab: #e6ebe8;
  }
  * { box-sizing: border-box; margin: 0; padding: 0; }
  html, body { width: 1200px; height: 900px; overflow: hidden; }
  body {
    position: relative;
    font-family: 'Roboto', sans-serif;
    background:
      radial-gradient(circle at 100% 28%, rgba(250,215,200,0.8), transparent 35%),
      radial-gradient(circle at 15% 80%, rgba(150,185,175,0.6), transparent 45%),
      linear-gradient(180deg, #c9d7d2 0%, #cfdcd8 40%, #b9ccc9 75%, #a2bcc0 100%);
  }
  .hero {
    position: absolute; left: 0; top: 0; width: 1200px; height: 250px;
    background:
      radial-gradient(circle at 30% 50%, rgba(120,110,95,0.75), transparent 30%),
      radial-gradient(circle at 75% 40%, rgba(140,205,170,0.8), transparent 35%),
      linear-gradient(90deg, #3f7d62 0%, #6f8a78 35%, #7cc49c 65%, #5fa98c 100%);
  }
  .status-bar {
    position: absolute; left: 0; top: 0; width: 1200px; height: 38px;
    color: #fff; font-size: 18px; display: flex; align-items: center; padding: 0 18px;
  }
  .status-bar .time { position: absolute; left: 0; width: 100%; text-align: center; font-weight: 500; }
  .status-bar .right { margin-left: auto; display: flex; align-items: center; gap: 8px; }
  .avatar {
    position: absolute; left: 544px; top: 56px; width: 112px; height: 112px; border-radius: 50%;
    background: radial-gradient(circle at 50% 45%, #d9a78e, #8a5a3e 75%);
  }
  .edit-badge {
    position: absolute; left: 636px; top: 70px; width: 22px; height: 22px; border-radius: 50%;
    background: #e0161c; border: 2px solid #fff;
  }
  .client-name { position: absolute; top: 177px; width: 1200px; text-align: center; color: #fff; font-size: 21px; }
  .client-phone { position: absolute; top: 206px; width: 1200px; text-align: center; color: var(--cyan); font-size: 15.5px; }
  .update-btn {
    position: absolute; left: 1004px; top: 182px; width: 168px; height: 42px;
    background: var(--blue); color: #fff; font-size: 16px; letter-spacing: 0.5px;
    display: flex; align-items: center; justify-content: center; gap: 12px;
    box-shadow: 0 2px 3px rgba(0,0,0,0.3);
  }
  .tabs { position: absolute; left: 0; top: 250px; width: 1200px; height: 63px; display: flex; }
  .tab {
    flex: 1; display: flex; align-items: center; justify-content: center; gap: 12px;
    background: var(--tab); color: var(--ink); font-size: 21px; border-left: 1px solid #d3dad6;
  }
  .tab.active { background: var(--green); color: #fff; border-left: 0; }
  .field {
    position: absolute; height: 70px; background: var(--field);
    border: 1px solid var(--field-line); display: flex; align-items: center;
  }
  .field .icon {
    width: 78px; height: 48px; display: flex; align-items: center; justify-content: center;
    border-right: 1px solid rgba(160,170,168,0.5);
  }
  .field .label { padding-left: 21px; font-size: 18px; color: var(--label); }
  .field.cut { height: 19px; top: 313px; border-top: 0; }
  .field.cut .icon { height: 8px; align-self: flex-start; }
  .section-title { position: absolute; left: 19px; top: 393px; font-size: 22px; color: var(--ink); }
  svg { display: block; }
</style>
</head>
<body>
  <header class="hero" role="img" aria-label="Blurred photo backdrop in green tones"></header>

  <div class="status-bar">
    <span>Tablet</span>
    <svg width="20" height="16" viewBox="0 0 20 16" style="margin-left:8px"><path d="M2 6a12 12 0 0 1 16 0M5 9a8 8 0 0 1 10 0M8 12a4 4 0 0 1 4 0" stroke="#fff" stroke-width="2" fill="none"/></svg>
    <span class="time">4:21 PM</span>
    <span class="right">
      <svg width="10" height="18" viewBox="0 0 10 18"><path d="M1 5l8 7-4 4V2l4 4-8 7" stroke="#cfe" stroke-width="1.4" fill="none"/></svg>
      <span>100%</span>
      <svg width="38" height="16" viewBox="0 0 38 16"><rect x="1" y="1" width="33" height="14" rx="3" fill="none" stroke="#fff"/><rect x="3" y="3" width="29" height="10" rx="2" fill="#fff"/><rect x="35" y="5" width="2" height="6" fill="#fff"/></svg>
    </span>
  </div>

  <div class="avatar" role="img" aria-label="Client profile photo"></div>
  <div class="edit-badge">
    <svg width="18" height="18" viewBox="0 0 18 18"><path d="M5 13l1-3 5-5 2 2-5 5z" fill="#fff"/></svg>
  </div>
  <div class="client-name">Dana Whitlow</div>
  <div class="client-phone">04 555 010 2287</div>
  <div class="update-btn">UPDATE
    <svg width="24" height="24" viewBox="0 0 24 24"><path d="M9 3.5A9 9 0 0 0 7 20M15 20.5A9 9 0 0 0 17 4M7 20l-3-1M17 4l3 1" stroke="#fff" stroke-width="1.6" fill="none"/></svg>
  </div>

  <nav class="tabs">
    <div class="tab active">
      <svg width="20" height="16" viewBox="0 0 20 16"><rect x="1" y="1" width="18" height="14" fill="none" stroke="#fff" stroke-width="1.5"/><circle cx="6" cy="6.5" r="2" fill="#fff"/><path d="M3 12a3 3 0 0 1 6 0zM11 5h6M11 8h6M11 11h6" stroke="#fff" stroke-width="1.4" fill="#fff"/></svg>
      Contact</div>
    <div class="tab">
      <svg width="22" height="22" viewBox="0 0 22 22"><path d="M4 6a9 9 0 1 0 4-3" stroke="#333" stroke-width="1.8" fill="none"/><text x="11" y="14" font-size="7" text-anchor="middle" fill="#333" font-family="Roboto, sans-serif">24</text></svg>
      Service</div>
    <div class="tab">
      <svg width="10" height="20" viewBox="0 0 10 20"><rect x="1" y="1" width="8" height="18" rx="2" fill="#333"/><circle cx="5" cy="6" r="1.5" fill="#e6ebe8"/><circle cx="5" cy="10" r="1.5" fill="#e6ebe8"/><circle cx="5" cy="14" r="1.5" fill="#e6ebe8"/></svg>
      Permission</div>
    <div class="tab">
      <svg width="20" height="18" viewBox="0 0 20 18"><path d="M1 1v16h18M4 15V9M8 15V6M12 15V10M16 15V4M3 9l5-4 4 5 5-6" stroke="#333" stroke-width="1.4" fill="none"/></svg>
      Financial</div>
  </nav>

  <div class="field cut" style="left:18px;width:377px"><div class="icon"></div></div>
  <div class="field cut" style="left:411px;width:378px"><div class="icon"></div></div>
  <div class="field cut" style="left:804px;width:378px"><div class="icon"></div></div>

  <h2 class="section-title" style="font-weight:400">Emergency Contact</h2>

  <div class="field" style="left:18px;top:448px;width:377px">
    <div class="icon"><svg width="40" height="38" viewBox="0 0 40 38"><circle cx="20" cy="12" r="9" fill="none" stroke="var(--icon)" stroke-width="1.6"/><path d="M3 36c0-9 8-12 17-12s17 3 17 12z" fill="none" stroke="var(--icon)" stroke-width="1.6"/></svg></div>
    <span class="label">First Name</span></div>
  <div class="field" style="left:411px;top:448px;width:378px">
    <div class="icon"><svg width="40" height="38" viewBox="0 0 40 38"><circle cx="20" cy="12" r="9" fill="none" stroke="var(--icon)" stroke-width="1.6"/><path d="M3 36c0-9 8-12 17-12s17 3 17 12z" fill="none" stroke="var(--icon)" stroke-width="1.6"/></svg></div>
    <span class="label">Last Name</span></div>
  <div class="field" style="left:804px;top:448px;width:378px">
    <div class="icon"><svg width="34" height="32" viewBox="0 0 34 32"><g fill="var(--icon)"><circle cx="8" cy="5" r="3.5"/><circle cx="26" cy="5" r="3.5"/><circle cx="17" cy="20" r="3.5"/><rect x="2" y="10" width="12" height="7" rx="3"/><rect x="20" y="10" width="12" height="7" rx="3"/><rect x="11" y="25" width="12" height="7" rx="3"/></g></svg></div>
    <span class="label">Relationship</span></div>

  <div class="field" style="left:18px;top:536px;width:1166px">
    <div class="icon"><svg width="40" height="38" viewBox="0 0 40 38"><path d="M20 26c-6-7-9-11-9-15a9 9 0 0 1 18 0c0 4-3 8-9 15z" fill="none" stroke="var(--icon)" stroke-width="1.8"/><circle cx="20" cy="11" r="3.5" fill="var(--icon)"/><path d="M11 24H5l-3 12h36l-3-12h-6" fill="none" stroke="var(--icon)" stroke-width="1.6"/></svg></div>
    <span class="label">Address</span></div>

  <div class="field" style="left:18px;top:624px;width:575px">
    <div class="icon"><svg width="30" height="30" viewBox="0 0 30 30"><g fill="var(--icon)"><rect x="1" y="1" width="7" height="7"/><rect x="10" y="11" width="7" height="7"/></g><rect x="20" y="21" width="7" height="7" fill="none" stroke="var(--icon)" stroke-width="1.5"/><path d="M5 8v6h5M14 18v6h6" stroke="var(--icon)" stroke-width="1.5" fill="none"/></svg></div>
    <span class="label">Suburb</span></div>
  <div class="field" style="left:610px;top:624px;width:574px">
    <div class="icon"><svg width="42" height="24" viewBox="0 0 42 24"><rect x="1" y="1" width="40" height="22" rx="4" fill="none" stroke="var(--icon)" stroke-width="1.6"/><text x="21" y="18" font-size="16" text-anchor="middle" fill="var(--icon)" font-family="Roboto, sans-serif">ZIP</text></svg></div>
    <span class="label">Post Code</span></div>

  <div class="field" style="left:18px;top:712px;width:377px">
    <div class="icon"><svg width="38" height="26" viewBox="0 0 38 26"><rect x="1" y="1" width="36" height="24" fill="none" stroke="var(--icon)" stroke-width="1.6"/><path d="M1 1l18 14L37 1M1 25l13-13M37 25L24 12" stroke="var(--icon)" stroke-width="1.6" fill="none"/></svg></div>
    <span class="label">Email</span></div>
  <div class="field" style="left:411px;top:712px;width:378px">
    <div class="icon"><svg width="22" height="36" viewBox="0 0 22 36"><rect x="1" y="1" width="20" height="34" rx="3" fill="none" stroke="var(--icon)" stroke-width="1.8"/><path d="M1 6h20M1 28h20" stroke="var(--icon)" stroke-width="1.4"/><circle cx="11" cy="31.5" r="1.5" fill="var(--icon)"/></svg></div>
    <span class="label">Mobile</span></div>
  <div class="field" style="left:804px;top:712px;width:378px">
    <div class="icon"><svg width="34" height="34" viewBox="0 0 34 34"><path d="M7 2l5 7-3 3c2 5 6 9 11 11l3-3 7 5-4 6C15 30 4 19 1 6z" fill="none" stroke="var(--icon)" stroke-width="1.6"/><path d="M19 8a7 7 0 0 1 7 7M20 3a12 12 0 0 1 11 11" stroke="var(--icon)" stroke-width="1.4" fill="none"/></svg></div>
    <span class="label">Landline</span></div>

  <div class="field" style="left:18px;top:798px;width:1166px">
    <div class="icon"><svg width="36" height="36" viewBox="0 0 36 36"><circle cx="12" cy="6" r="3.5" fill="var(--icon)"/><path d="M8 11l6 1 3 6-4 4 3 10M12 13l-5 8-5 1M13 22l-6 11" stroke="var(--icon)" stroke-width="3" fill="none" stroke-linecap="round"/><rect x="17" y="18" width="8" height="7" fill="var(--icon)"/><circle cx="28" cy="7" r="5.5" fill="none" stroke="var(--icon)" stroke-width="1.3"/><path d="M28 4v3h2" stroke="var(--icon)" stroke-width="1.2" fill="none"/></svg></div>
    <span class="label">Work</span></div>
</body>
</html>
```